Business Card Design

New business card design

Target Market(s)

Residential & Commercial Property Managers

Industry/Entity Type

Plumbing Services

Contact Information for Business Card

Name - Rowan Keddle, title - Director, Phone Number - 0431 286 517, email - rowan@tbk-plumbing.com.au, Company ABN - 73 215 904 386,

Font styles to use
Sans Serif

Colors
0054AA
0677BA
7BADD7
CADEEF
E8F1F8

```html
<!DOCTYPE html>
<html lang="en">
<head>
<meta charset="utf-8">
<title>TBK Plumbing Services – Business Card</title>
<link rel="stylesheet" href="https://fonts.googleapis.com/css2?family=Montserrat:wght@400;500;700&display=swap">
<style>
  :root {
    --backdrop: #1b1c1e;
    --card-light: #f3f3f3;
    --card-dark: #1d232a;
    --ink: #1d232a;
    --brand-blue: #29a3dc;
    --muted: #5a524b;
    --white: #ffffff;
  }
  * { margin: 0; padding: 0; box-sizing: border-box; }
  html, body {
    width: 1200px; height: 1059px; overflow: hidden;
    background: var(--backdrop);
    font-family: "Montserrat", sans-serif;
  }
  .card {
    position: absolute;
    width: 690px; height: 392px;
    border-radius: 18px;
    overflow: hidden;
  }
  .card--front { left: 256px; top: 89px; background: var(--card-light); }
  .card--back  { left: 255px; top: 547px; background: var(--card-dark); }

  .brand {
    position: absolute; left: 0; right: 0;
    text-align: center;
  }
  .brand__name {
    display: inline-flex; align-items: center; gap: 14px;
    font-weight: 500; font-size: 70px; letter-spacing: 10px;
    line-height: 1;
  }
  .brand__dot {
    width: 20px; height: 20px; border-radius: 50%;
    background: var(--brand-blue);
  }
  .brand__tagline {
    display: block;
    font-weight: 400; font-size: 13px; letter-spacing: 12px;
    text-transform: lowercase;
  }
  .card--front .brand { top: 74px; }
  .card--front .brand__name { color: var(--ink); }
  .card--front .brand__tagline { color: var(--muted); margin-top: 28px; }
  .card--back .brand { top: 160px; }
  .card--back .brand__name { color: var(--white); font-size: 76px; }
  .card--back .brand__tagline { color: var(--white); margin-top: 30px; font-size: 14px; letter-spacing: 14px; }

  .person {
    position: absolute; right: 374px; top: 258px;
    text-align: right;
  }
  .person__name { color: var(--brand-blue); font-weight: 700; font-size: 28px; line-height: 1.1; }
  .person__title { color: var(--ink); font-size: 16px; margin-top: 2px; }

  .divider {
    position: absolute; left: 343px; top: 252px;
    width: 1px; height: 72px; background: var(--brand-blue);
  }

  .contact {
    position: absolute; left: 366px; top: 246px;
    list-style: none; color: var(--ink); font-size: 17px;
  }
  .contact li { display: flex; align-items: center; gap: 8px; height: 26px; }
  .contact li + li { margin-top: 0; }
  .contact .contact__abn { margin-bottom: 10px; }
  .contact__label { color: var(--brand-blue); }
  .contact svg { width: 13px; height: 13px; fill: var(--brand-blue); flex: none; }

  .footer-band {
    position: absolute; left: 0; bottom: 0;
    width: 690px; height: 17px;
  }
</style>
</head>
<body>

<section class="card card--front">
  <div class="brand">
    <span class="brand__name">TBK<span class="brand__dot"></span></span>
    <span class="brand__tagline">plumbing services</span>
  </div>

  <div class="person">
    <p class="person__name">Rowan Keddle</p>
    <p class="person__title">Director</p>
  </div>

  <div class="divider"></div>

  <ul class="contact">
    <li class="contact__abn"><span class="contact__label">ABN</span>&nbsp;-&nbsp;73 215 904 386</li>
    <li>
      <svg viewBox="0 0 24 24" aria-hidden="true"><path d="M6.6 10.8a15.1 15.1 0 0 0 6.6 6.6l2.2-2.2a1 1 0 0 1 1-.25 11.4 11.4 0 0 0 3.6.57 1 1 0 0 1 1 1V20a1 1 0 0 1-1 1A17 17 0 0 1 3 4a1 1 0 0 1 1-1h3.5a1 1 0 0 1 1 1c0 1.25.2 2.45.57 3.57a1 1 0 0 1-.25 1z"/></svg>
      0431 286 517
    </li>
    <li>
      <svg viewBox="0 0 24 24" aria-hidden="true"><path d="M2 5h20v14H2z M2 5l10 8 10-8" fill="none" stroke="#29a3dc" stroke-width="0"/><path d="M2 5h20l-10 8zM2 7l7 5.5L2 18zM22 7v11l-7-5.5zM10.3 13.5 12 15l1.7-1.5L22 19H2z"/></svg>
      rowan@tbk-plumbing.com.au
    </li>
  </ul>

  <svg class="footer-band" viewBox="0 0 690 17" preserveAspectRatio="none" aria-hidden="true">
    <polygon points="0,0 348,0 326,17 0,17" fill="#1d232a"/>
    <polygon points="348,0 362,0 340,17 326,17" fill="#ffffff"/>
    <polygon points="362,0 690,0 690,17 340,17" fill="#29a3dc"/>
  </svg>
</section>

<section class="card card--back">
  <div class="brand">
    <span class="brand__name">TBK<span class="brand__dot"></span></span>
    <span class="brand__tagline">plumbing services</span>
  </div>
</section>

</body>
</html>
```